Vantoq Business Card Project showing the logo and a marbo image on the rear

Design a whacky but professional business card, the logo is for the front and the Marbo image is for the rear. Happy to consider other open source Marbo Images if the designer wants to select one from the web. Vantoq is a competitor to OMB.com.au and Pellory.com.au and is based around every property in Australia

Target Market(s)

Business

Contact Information for Business Card

Name, Title, Email, Web, Phone Number

Font styles to use
Other font styles liked:
• avenir

Requirements
Must have
• Image on Back logo on front
Nice to have
• Happy to consider other images on rear, preftably Colin Marbo. Image supplied I own, we can use open source other Marbo Images

```html
<!DOCTYPE html>
<html lang="en">
<head>
<meta charset="utf-8">
<title>Vantoq Business Card</title>
<link href="https://fonts.googleapis.com/css2?family=Outfit:wght@500&family=Roboto:wght@400;700&display=swap" rel="stylesheet">
<style>
  :root {
    --bg: #1c1c1c;
    --card: #f1f1f0;
    --ink: #111111;
    --black: #0b0b0b;
    --orange: #f18d0c;
    --white: #ffffff;
  }
  html, body {
    margin: 0;
    width: 1200px;
    height: 1138px;
    overflow: hidden;
    background: var(--bg);
    font-family: "Roboto", sans-serif;
  }
  .card {
    position: absolute;
    width: 620px;
    height: 375px;
    border-radius: 14px;
    overflow: hidden;
    background: var(--card);
  }
  .card--front { left: 274px; top: 186px; }
  .card--back { left: 276px; top: 608px; }

  .front-brand {
    position: absolute;
    top: 72px;
    left: 0;
    width: 100%;
    text-align: center;
  }
  .front-brand__name {
    display: inline-flex;
    align-items: center;
    gap: 18px;
    font-family: "Roboto", sans-serif;
    font-weight: 700;
    font-size: 62px;
    line-height: 1;
    color: var(--ink);
  }
  .brand-square {
    display: inline-block;
    width: 52px;
    height: 52px;
    background: var(--orange);
  }
  .front-brand__url {
    margin-top: 14px;
    font-size: 15px;
    letter-spacing: 0.72em;
    color: var(--ink);
    padding-left: 0.72em;
  }
  .cityscape {
    position: absolute;
    left: 0;
    bottom: 0;
    width: 100%;
    height: 178px;
    background: linear-gradient(180deg, #f1f1f0 0%, #e84a8a 18%, #f0a13a 38%, #9bd046 58%, #3aa0d8 76%, #e7e14a 88%, #6cbf3c 100%);
  }

  .back-shapes { position: absolute; inset: 0; }
  .back-logo {
    position: absolute;
    left: 0;
    top: 0;
    width: 290px;
    height: 375px;
    display: flex;
    flex-direction: column;
    align-items: center;
    justify-content: center;
    gap: 16px;
  }
  .back-logo .brand-square { width: 90px; height: 90px; }
  .back-logo__name {
    font-family: "Roboto", sans-serif;
    font-weight: 700;
    font-size: 38px;
    color: var(--white);
  }
  .contact {
    position: absolute;
    left: 369px;
    top: 66px;
    color: var(--ink);
  }
  .contact__name {
    font-family: "Outfit", sans-serif;
    font-weight: 500;
    font-size: 26px;
    color: var(--orange);
    line-height: 1.1;
  }
  .contact__title { font-size: 16px; margin-top: 3px; }
  .contact__list { list-style: none; margin: 28px 0 0; padding: 0; }
  .contact__list li {
    display: flex;
    align-items: center;
    gap: 16px;
    font-size: 16px;
    height: 23px;
    margin-left: 0;
  }
  .contact__list svg { width: 15px; height: 15px; flex: none; margin-left: 2px; }
  .accent { color: var(--orange); }
  .contact__address { font-size: 16px; line-height: 20px; margin-top: 14px; }
  .tagline {
    position: absolute;
    left: 360px;
    width: 200px;
    top: 320px;
    text-align: center;
    font-size: 16px;
    color: var(--white);
    white-space: nowrap;
  }
</style>
</head>
<body>

<section class="card card--front">
  <div class="front-brand">
    <div class="front-brand__name"><span class="brand-square"></span>Vantoq</div>
    <div class="front-brand__url">www.vantoq.com</div>
  </div>
  <div class="cityscape" role="img" aria-label="Colourful cartoon city skyline with buildings and a row of trams, in the style of Colin Marbo"></div>
</section>

<section class="card card--back">
  <svg class="back-shapes" width="620" height="375" viewBox="0 0 620 375">
    <rect x="290" y="312" width="330" height="38" fill="var(--orange)"/>
    <path d="M256 0 C344 80 356 290 266 375 H0 V0 Z" fill="var(--orange)"/>
    <path d="M248 0 C330 80 338 290 244 375 H0 V0 Z" fill="var(--black)"/>
  </svg>
  <div class="back-logo">
    <span class="brand-square"></span>
    <div class="back-logo__name">Vantoq</div>
  </div>
  <div class="contact">
    <div class="contact__name">Colm Dorsett</div>
    <div class="contact__title">Founder &amp; CEO</div>
    <ul class="contact__list">
      <li>
        <svg viewBox="0 0 16 16"><circle cx="8" cy="8" r="7" fill="none" stroke="var(--orange)" stroke-width="1.4"/><path d="M5.5 4.5 L7 6 L6.2 7.2 Q7 9 8.8 9.8 L10 9 L11.5 10.5 L10.5 11.6 Q6 10.8 4.4 5.6 Z" fill="var(--orange)"/></svg>
        (00) 4818 5070
      </li>
      <li>
        <svg viewBox="0 0 16 16"><rect x="1" y="3" width="14" height="10" fill="var(--orange)"/><path d="M1.5 3.5 L8 9 L14.5 3.5" fill="none" stroke="var(--white)" stroke-width="1.3"/></svg>
        dorsett@vantoq.com
      </li>
      <li>
        <svg viewBox="0 0 16 16"><circle cx="8" cy="8" r="7" fill="var(--orange)"/><path d="M1 8 H15 M8 1 Q4 8 8 15 M8 1 Q12 8 8 15" fill="none" stroke="var(--white)" stroke-width="0.9"/></svg>
        <span>www.<span class="accent">vantoq</span>.com</span>
      </li>
    </ul>
    <div class="contact__address">Level 4, 18 Calder Lane,<br>Sydney 2000, Australia</div>
  </div>
  <div class="tagline">Buying, Selling and Research</div>
</section>

</body>
</html>
```